hotel amenities supply company needs design for bottles and accessories

we need to design four 30ml amenity tubes branded "ORVELLE" , shampoo, shower gel, conditioner and body lotion. the bottle has to be somewhat clear to be able to see the liquid inside. its basically designing the complete identity for "orvelle". attached are some examples. also the accessory boxes should match the design eg, shaving kit,vanity kit, toothbrush etc

Target Market(s)

hotels

Industry/Entity Type

Hotel

Font styles to use
Script

Requirements
Must have
• name "orvelle " on bottles and product info
Should not have
• dark colors

```html
<!DOCTYPE html>
<html lang="en">
<head>
<meta charset="utf-8">
<title>Orvelle Amenity Tubes</title>
<link rel="stylesheet" href="https://fonts.googleapis.com/css2?family=Kaushan+Script&family=Josefin+Sans:wght@300;400&family=Playball&display=swap">
<style>
  :root {
    --bg-top: #eefcff;
    --bg-bottom: #ffffff;
    --crimp: #ececec;
    --cap: #efefef;
    --cap-band: #b9b9b9;
    --ink: #2b2b2b;
    --white: #ffffff;
    --green-body: #dde8b3;
    --green-band: #9bd01c;
    --green-dot: #b7d94a;
    --lilac-body: #f3f3f3;
    --lilac-band: #8c85cc;
    --lilac-dot: #9a8fdd;
    --gold-body: #f3f3f3;
    --gold-band: #ffc20e;
    --gold-dot: #f4c21a;
    --teal-body: #cbe8f8;
    --teal-band: #25906f;
    --teal-dot: #2f9a7c;
  }
  * { margin: 0; padding: 0; box-sizing: border-box; }
  html, body { width: 1200px; height: 1200px; overflow: hidden; }
  body {
    background: linear-gradient(180deg, var(--bg-top) 0%, #f4feff 40%, var(--bg-bottom) 80%);
    position: relative;
  }
  .tube {
    position: absolute;
    top: 232px;
    width: 276px;
    height: 740px;
  }
  .tube--shampoo { left: 32px; --body: var(--green-body); --band: var(--green-band); --dot: var(--green-dot); }
  .tube--conditioner { left: 317px; --body: var(--lilac-body); --band: var(--lilac-band); --dot: var(--lilac-dot); }
  .tube--lotion { left: 602px; --body: var(--gold-body); --band: var(--gold-band); --dot: var(--gold-dot); }
  .tube--gel { left: 887px; --body: var(--teal-body); --band: var(--teal-band); --dot: var(--teal-dot); }

  .tube__crimp {
    position: absolute; left: 0; top: 0; width: 276px; height: 30px;
    background: var(--crimp); border-radius: 3px;
  }
  .tube__body {
    position: absolute; left: 0; top: 28px; width: 276px; height: 602px;
    background: var(--body);
    clip-path: polygon(0 0, 100% 0, 96% 35%, 78% 100%, 22% 100%, 4% 35%);
  }
  .tube__logo {
    position: absolute; left: 0; width: 276px; top: 168px;
    text-align: center;
    font-family: "Kaushan Script", cursive;
    font-size: 64px; color: var(--ink); line-height: 1;
  }
  .tube__logo-dot {
    position: absolute; top: 174px; left: 180px;
    width: 18px; height: 18px; border-radius: 50%;
    background: var(--dot);
  }
  .tube__band {
    position: absolute; left: 40px; top: 340px; width: 200px; height: 84px;
    background: var(--band);
    color: var(--white); text-align: center;
  }
  .tube__name {
    display: inline-block; margin-top: 16px; padding: 0 8px 2px;
    font-family: "Josefin Sans", sans-serif; font-weight: 400;
    font-size: 24px; letter-spacing: -0.5px;
    border-bottom: 1px solid var(--white); line-height: 1.1;
  }
  .tube__variant {
    display: block; margin-top: 2px;
    font-family: "Playball", cursive; font-size: 23px;
  }
  .tube__pattern {
    position: absolute; left: 36px; top: 424px; width: 208px; height: 76px;
    background: linear-gradient(180deg, var(--dot) 0%, transparent 100%);
    opacity: 0.45;
  }
  .tube__volume {
    position: absolute; left: 0; width: 276px; top: 566px;
    text-align: center;
    font-family: "Josefin Sans", sans-serif; font-size: 17px; line-height: 1.2;
    color: var(--ink);
  }
  .tube__cap {
    position: absolute; left: 62px; top: 630px; width: 152px; height: 108px;
    background: linear-gradient(90deg, #e4e4e4, var(--cap) 40%, #fafafa 60%, #e0e0e0);
    border-radius: 0 0 16px 16px;
  }
  .tube__cap::before {
    content: ""; position: absolute; left: 0; top: 0; width: 100%; height: 12px;
    background: linear-gradient(90deg, #8a8a8a, #f5f5f5 30%, var(--cap-band) 55%, #fafafa 75%, #7e7e7e);
  }
</style>
</head>
<body>
  <div class="tube tube--shampoo">
    <div class="tube__crimp"></div>
    <div class="tube__body"></div>
    <div class="tube__logo">Orvelle</div>
    <div class="tube__logo-dot"></div>
    <div class="tube__band"><span class="tube__name">SHAMPOO</span><span class="tube__variant">green tea</span></div>
    <div class="tube__pattern" role="img" aria-label="Decorative swirl pattern in green"></div>
    <div class="tube__volume">30 ml<br>1 fl. oz.</div>
    <div class="tube__cap"></div>
  </div>
  <div class="tube tube--conditioner">
    <div class="tube__crimp"></div>
    <div class="tube__body"></div>
    <div class="tube__logo">Orvelle</div>
    <div class="tube__logo-dot"></div>
    <div class="tube__band"><span class="tube__name">CONDITIONER</span><span class="tube__variant">for hair</span></div>
    <div class="tube__pattern" role="img" aria-label="Decorative swirl pattern in lilac"></div>
    <div class="tube__volume">30 ml<br>1 fl. oz.</div>
    <div class="tube__cap"></div>
  </div>
  <div class="tube tube--lotion">
    <div class="tube__crimp"></div>
    <div class="tube__body"></div>
    <div class="tube__logo">Orvelle</div>
    <div class="tube__logo-dot"></div>
    <div class="tube__band"><span class="tube__name">BODY LOTION</span><span class="tube__variant">milk &amp; honey</span></div>
    <div class="tube__pattern" role="img" aria-label="Decorative swirl pattern in golden yellow"></div>
    <div class="tube__volume">30 ml<br>1 fl. oz.</div>
    <div class="tube__cap"></div>
  </div>
  <div class="tube tube--gel">
    <div class="tube__crimp"></div>
    <div class="tube__body"></div>
    <div class="tube__logo">Orvelle</div>
    <div class="tube__logo-dot"></div>
    <div class="tube__band"><span class="tube__name">SHOWER GEL</span><span class="tube__variant">ocean fresh</span></div>
    <div class="tube__pattern" role="img" aria-label="Decorative swirl pattern in teal"></div>
    <div class="tube__volume">30 ml<br>1 fl. oz.</div>
    <div class="tube__cap"></div>
  </div>
</body>
</html>
```